Custom Seed Packet design for Flower Farm

We need a design for our seeds packets.
The design will be a kind of "fill in the blanks" as we need the design to be adaptable for multiple varieties of seed. We will be using the design for a rubber stamp.
Our seed packets are 90x90mm in size.
Black logo only. No colour required.
A vintage botanical influence is desired.
Will need to include the following info,
"Wrenfield Gable Co logo" , "Seeds", "Plant Type", "Variety", "Harvested"

```html
<!DOCTYPE html>
<html lang="en">
<head>
<meta charset="utf-8">
<title>Flower Seeds Packet Label – Wrenfield Gable Co</title>
<link href="https://fonts.googleapis.com/css2?family=Great+Vibes&family=Open+Sans:wght@400&display=swap" rel="stylesheet">
<style>
  :root {
    --page: #ffffff;
    --ink: #141210;
    --frame-dark: #0e0c0a;
    --frame-mid: #2a2520;
    --parchment: #d9c7a4;
    --parchment-light: #e3d4b6;
    --flora-tone: #c4b08a;
    --band-text: #d8c08e;
  }
  * { box-sizing: border-box; margin: 0; padding: 0; }
  html, body {
    width: 1122px;
    height: 1200px;
    overflow: hidden;
    background: var(--page);
  }
  .canvas {
    position: relative;
    width: 1122px;
    height: 1200px;
  }
  .label {
    position: absolute;
    left: 61px;
    top: 100px;
    width: 1000px;
    height: 1000px;
  }
  .label__frame {
    position: absolute;
    inset: 0;
    background: radial-gradient(circle at 50% 50%, var(--frame-mid), var(--frame-dark) 70%);
  }
  .panel {
    position: absolute;
    left: 107px;
    top: 107px;
    width: 784px;
    height: 788px;
    background: radial-gradient(ellipse at 50% 40%, var(--parchment-light), var(--parchment) 75%);
    color: var(--ink);
  }
  .corner-flora {
    position: absolute;
    width: 200px;
    height: 140px;
    border-radius: 50%;
    background: radial-gradient(ellipse, var(--flora-tone), transparent 70%);
  }
  .corner-flora--tl { left: 0; top: 0; }
  .corner-flora--tr { right: 0; top: 0; }
  .corner-flora--bl { left: 0; bottom: 10px; }
  .corner-flora--br { right: 0; bottom: 10px; }
  .title {
    position: absolute;
    left: 0;
    right: 0;
    top: 58px;
    text-align: center;
    font-family: "Great Vibes", cursive;
    line-height: 1;
  }
  .title__small {
    display: block;
    font-size: 40px;
    margin-left: 80px;
  }
  .title__main {
    display: block;
    font-size: 150px;
    margin-top: -38px;
  }
  .fields {
    position: absolute;
    left: 14px;
    right: 14px;
    top: 260px;
    font-family: "Open Sans", sans-serif;
    font-size: 23px;
  }
  .field {
    display: flex;
    align-items: flex-end;
    height: 32px;
    margin-bottom: 34px;
  }
  .field__rule {
    flex: 1;
    margin-left: 8px;
    border-bottom: 1.5px solid var(--ink);
    margin-bottom: 4px;
  }
  .garden-band {
    position: absolute;
    left: 0;
    right: 0;
    top: 495px;
    height: 45px;
    background: var(--frame-dark);
    color: var(--band-text);
    font-family: "Great Vibes", cursive;
    font-size: 36px;
    line-height: 45px;
    text-align: center;
  }
  .maker {
    position: absolute;
    left: 0;
    right: 0;
    top: 690px;
    text-align: center;
    font-family: "Open Sans", sans-serif;
    font-size: 24px;
    color: var(--ink);
    letter-spacing: 1px;
  }
</style>
</head>
<body>
<main class="canvas">
  <section class="label">
    <div class="label__frame" role="img" aria-label="Black frame filled with cream vintage scrollwork ornament"></div>
    <div class="panel">
      <div class="corner-flora corner-flora--tl" role="img" aria-label="Line-drawn botanical flower cluster"></div>
      <div class="corner-flora corner-flora--tr" role="img" aria-label="Line-drawn botanical flower cluster"></div>
      <div class="corner-flora corner-flora--bl" role="img" aria-label="Line-drawn botanical flower cluster"></div>
      <div class="corner-flora corner-flora--br" role="img" aria-label="Line-drawn botanical flower cluster"></div>

      <h1 class="title">
        <span class="title__small">Flower</span>
        <span class="title__main">Seeds</span>
      </h1>

      <div class="fields">
        <div class="field"><span class="field__label">Plant Type</span><span class="field__rule"></span></div>
        <div class="field"><span class="field__label">Variety</span><span class="field__rule"></span></div>
        <div class="field"><span class="field__label">Harvested</span><span class="field__rule"></span></div>
      </div>

      <div class="garden-band">from the garden of</div>

      <p class="maker">Wrenfield Gable Co. Flower Farm</p>
    </div>
  </section>
</main>
</body>
</html>
```